Walk Beside The River

Business Card design

Target Market(s)

People who require support in the commnity

Industry/Entity Type

Mental Health Support

Contact Information for Business Card

Mental Health Support Rosalind Tavener walkbesidetheriver@mailcove.com.au 0481 637 092 PO Box 926 Tallowmere QLD 4673

Colors
6B429C
8869AF
B7A5CE
E3DAEB
F3F0F8

Requirements
Must have
• Logo & details listed above
Should not have
• No red or orange

```html
<!DOCTYPE html>
<html lang="en">
<head>
<meta charset="utf-8">
<title>Walk Beside The River – Business Card</title>
<link rel="stylesheet" href="https://fonts.googleapis.com/css2?family=Open+Sans:wght@400;600;800&display=swap">
<style>
  :root {
    --stage: #232323;
    --card-dark: #1f1f22;
    --sun-yellow: #f2e935;
    --sun-gold: #e4b93a;
    --brand-purple: #6b429c;
    --cream: #f3f0f8;
    --ink: #1a1a1a;
  }
  * { box-sizing: border-box; margin: 0; padding: 0; }
  html, body {
    width: 1200px; height: 780px; overflow: hidden;
    background: var(--stage);
    font-family: "Open Sans", Arial, sans-serif;
  }
  .stage { position: relative; width: 1200px; height: 780px; }

  .card {
    position: absolute; width: 560px; height: 330px;
    border-radius: 22px; overflow: hidden;
    border: 3px solid var(--sun-yellow);
  }

  /* Back of card */
  .card--back { left: 320px; top: 40px; }
  .card__pattern {
    width: 100%; height: 100%;
    background: linear-gradient(200deg, #f6f07a 0%, var(--sun-yellow) 40%, #e9d23a 75%, var(--sun-gold) 100%);
  }

  /* Front of card */
  .card--front { left: 320px; top: 410px; background: var(--card-dark); }

  .identity { position: absolute; left: 0; top: 58px; display: flex; }
  .identity__accent { width: 18px; height: 62px; background: var(--sun-yellow); }
  .identity__text { padding-left: 14px; }
  .identity__name { font-weight: 800; font-size: 26px; line-height: 1.1; color: var(--sun-yellow); }
  .identity__name .surname { color: var(--brand-purple); }
  .identity__role { font-size: 14px; font-weight: 600; color: var(--cream); margin-top: 2px; }

  .brand {
    position: absolute; right: 40px; top: 26px;
    width: 170px; height: 170px; border-radius: 50%;
    background: var(--brand-purple);
    display: flex; align-items: center; justify-content: center; text-align: center;
  }
  .brand__name {
    font-weight: 600; font-size: 17px; line-height: 1.25;
    color: var(--cream); letter-spacing: 1.5px; text-transform: uppercase;
    width: 120px;
  }

  .contacts { position: absolute; left: 110px; top: 166px; list-style: none; }
  .contacts__item {
    display: flex; align-items: center; gap: 10px;
    font-size: 15px; color: var(--cream); line-height: 23px;
  }
  .contacts__icon { width: 14px; height: 14px; flex: none; }

  .tagline-band {
    position: absolute; left: 0; right: 0; top: 252px; height: 40px;
    background: var(--sun-yellow);
    display: flex; align-items: center; justify-content: flex-end; padding-right: 60px;
  }
  .tagline { font-size: 15px; font-weight: 600; color: var(--ink); }
</style>
</head>
<body>
<main class="stage">

  <section class="card card--back">
    <div class="card__pattern" role="img" aria-label="Repeating pattern of golden starbursts on a bright yellow field"></div>
  </section>

  <section class="card card--front">
    <div class="identity">
      <span class="identity__accent"></span>
      <div class="identity__text">
        <p class="identity__name">Vesna <span class="surname">Halloway</span></p>
        <p class="identity__role">CEO/Director</p>
      </div>
    </div>

    <div class="brand">
      <p class="brand__name">Walk Beside The River</p>
    </div>

    <ul class="contacts">
      <li class="contacts__item">
        <svg class="contacts__icon" viewBox="0 0 24 24" aria-hidden="true"><path fill="#f2e935" d="M6.6 10.8a15 15 0 0 0 6.6 6.6l2.2-2.2c.3-.3.7-.4 1-.2 1.1.4 2.3.6 3.6.6.6 0 1 .4 1 1V20c0 .6-.4 1-1 1A17 17 0 0 1 3 4c0-.6.4-1 1-1h3.5c.6 0 1 .4 1 1 0 1.3.2 2.5.6 3.6.1.3 0 .7-.2 1z"/></svg>
        <span>0481 637 092</span>
      </li>
      <li class="contacts__item">
        <svg class="contacts__icon" viewBox="0 0 24 24" aria-hidden="true"><rect x="2" y="5" width="20" height="14" rx="2" fill="none" stroke="#f2e935" stroke-width="2"/><path d="M3 6l9 7 9-7" fill="none" stroke="#f2e935" stroke-width="2"/></svg>
        <span>walkbesidetheriver@mailcove.com.au</span>
      </li>
      <li class="contacts__item">
        <svg class="contacts__icon" viewBox="0 0 24 24" aria-hidden="true"><path fill="none" stroke="#f2e935" stroke-width="2" d="M12 22s7-7 7-12a7 7 0 0 0-14 0c0 5 7 12 7 12z"/><circle cx="12" cy="10" r="2.5" fill="#f2e935"/></svg>
        <span>PO Box 926 Tallowmere QLD 4673</span>
      </li>
    </ul>

    <div class="tagline-band">
      <p class="tagline">Mental Health Support Rosalind Tavener</p>
    </div>
  </section>

</main>
</body>
</html>
```